Tallowmere Air Business Card Design

Design new, 2 sides, business cards for a residential and light commercial heating, air conditioning contractor.

Target Market(s)

Homeowners, small businesses

Industry/Entity Type

Business

Contact Information for Business Card

Dominic Westerhall
Phone - 862-415-2736
Email
Address - PO box 518
Brightwater NJ 07912
Website - www.TallowmereAirLLC.example

Requirements
Must have
• logo, company colors, standard size with no die cut, so I can use nova stamp

```html
<!DOCTYPE html>
<html lang="en">
<head>
<meta charset="utf-8">
<title>Tallowmere Air Business Card</title>
<link rel="stylesheet" href="https://fonts.googleapis.com/css2?family=Crimson+Pro:ital,wght@0,400;0,600;1,500&family=Arimo:wght@400&display=swap">
<style>
  :root {
    --stage: #7a0f22;
    --burgundy: #8a0f24;
    --cream: #f3dc8c;
    --gold: #ecc977;
    --orange: #e0661c;
    --slate: #3f3d5a;
    --ink: #4a4440;
    --rule: #b9a066;
  }
  * { box-sizing: border-box; margin: 0; padding: 0; }
  html, body {
    width: 1200px;
    height: 987px;
    overflow: hidden;
  }
  body {
    background: var(--stage);
    position: relative;
    font-family: "Arimo", Arial, sans-serif;
  }
  .card {
    position: absolute;
    width: 351px;
    height: 615px;
    box-shadow: 0 6px 18px rgba(0, 0, 0, 0.35);
  }
  .card--front {
    left: 231px;
    top: 209px;
    background: var(--burgundy);
  }
  .card--back {
    left: 617px;
    top: 252px;
    background: var(--cream);
  }
  .card > * {
    position: absolute;
    left: 0;
    right: 0;
    text-align: center;
  }
  .wordmark {
    font-family: "Crimson Pro", Georgia, serif;
    font-weight: 600;
    font-size: 44px;
    line-height: 50px;
    letter-spacing: 0.5px;
  }
  .card--front .wordmark { top: 278px; color: var(--gold); }
  .card--back .wordmark { top: 451px; color: var(--burgundy); }
  .tagline {
    top: 491px;
    font-family: "Crimson Pro", Georgia, serif;
    font-size: 17.5px;
    line-height: 21.5px;
    color: var(--gold);
  }
  .person-name {
    top: 54px;
    font-family: "Crimson Pro", Georgia, serif;
    font-weight: 600;
    font-size: 35px;
    line-height: 40px;
    color: var(--burgundy);
  }
  .person-role {
    top: 95px;
    font-family: "Crimson Pro", Georgia, serif;
    font-style: italic;
    font-weight: 500;
    font-size: 21px;
    line-height: 26px;
    color: var(--slate);
  }
  .divider { margin: 0 auto; }
  .divider--upper { top: 137px; }
  .divider--lower { top: 272px; }
  .contact {
    top: 165px;
    font-size: 15.5px;
    line-height: 23px;
    color: var(--ink);
  }
  .contact .label { color: var(--orange); }
  .website {
    top: 301px;
    font-size: 15.5px;
    line-height: 20px;
    letter-spacing: 0.4px;
    color: var(--orange);
  }
</style>
</head>
<body>
  <section class="card card--front" aria-label="Card front">
    <p class="wordmark">Tallowmere Air</p>
    <p class="tagline">Residential &amp; light<br>commercial heating<br>Air conditioning contractor</p>
  </section>

  <section class="card card--back" aria-label="Card back">
    <h1 class="person-name">Dominic Westerhall</h1>
    <p class="person-role">CEO/Founder</p>
    <svg class="divider divider--upper" width="150" height="10" viewBox="0 0 150 10" aria-hidden="true">
      <line x1="0" y1="5" x2="150" y2="5" stroke="#b9a066" stroke-width="1"/>
      <rect x="71" y="1" width="8" height="8" fill="#e0661c" transform="rotate(45 75 5)"/>
    </svg>
    <div class="contact">
      <p>PO box 518</p>
      <p>Brightwater NJ 07912</p>
      <p><span class="label">P.</span> 862 415 2736 <span class="label">M.</span> 862 415 2790</p>
      <p>dominic@tallowmereairllc.example</p>
    </div>
    <svg class="divider divider--lower" width="150" height="10" viewBox="0 0 150 10" aria-hidden="true">
      <line x1="0" y1="5" x2="150" y2="5" stroke="#b9a066" stroke-width="1"/>
      <rect x="71" y="1" width="8" height="8" fill="#e0661c" transform="rotate(45 75 5)"/>
    </svg>
    <p class="website">WWW.TALLOWMEREAIRLLC.EXAMPLE</p>
    <p class="wordmark">Tallowmere Air</p>
  </section>
</body>
</html>
```